Real Estate Sign to Help Modernize and Make it POP!

Design a sign style that would be good for marketing the sale or lease of properties. This will be 3 ' x 4' when printed and needs to look professional, modern, and catchy. It should us the company name, logo, and phone number at a minimum. Keep with the color scheme but open to varieties.

It will be printed and put in a large wooden frame as shown in one of the pictures.

Target Market(s)

Buyers and Tenants

Industry/Entity Type

Real Estate

Requirements
Must have
• company name, logo, and phone number
same color scheme as sign and website
Nice to have
• My Name, "Mervin Kalloway, CCIM"
Company Website
Ability to have an easy change from FOR SALE to FOR LEASE or FOR SALE/LEASE when I need to move this sign to a new property
An ability to have reflective colors printed on the contrast for cars to see at night
Should not have
• "Property Managed by"

```html
<!DOCTYPE html>
<html lang="en">
<head>
<meta charset="utf-8">
<title>Meridian Crest Realty – For Sale Sign</title>
<link href="https://fonts.googleapis.com/css2?family=Anton&family=Cinzel:wght@400&family=Poppins:wght@400&display=swap" rel="stylesheet">
<style>
  :root{
    --bg:#e4e4e4;
    --paper:#ffffff;
    --teal:#4b7371;
    --teal-dark:#42625f;
    --brand:#566b60;
    --ink:#5a5a5a;
  }
  *{margin:0;padding:0;box-sizing:border-box;}
  html,body{width:1200px;height:1200px;overflow:hidden;background:var(--bg);}
  .sign{
    position:absolute;left:40px;top:180px;width:1120px;height:840px;
    background:var(--paper);overflow:hidden;
  }
  .edge{position:absolute;left:0;width:100%;height:17px;background:var(--teal);}
  .edge--top{top:0;}
  .edge--bottom{bottom:0;height:16px;}

  .brand{position:absolute;left:206px;top:61px;display:flex;align-items:center;gap:22px;}
  .brand-dot{width:114px;height:114px;border-radius:50%;background:var(--brand);flex:none;}
  .brand-name{color:var(--brand);font-family:"Cinzel",serif;font-weight:400;text-align:center;}
  .brand-name .main{display:block;font-size:84px;line-height:1;letter-spacing:0.04em;}
  .brand-name .sub{display:flex;align-items:center;gap:14px;font-size:22px;letter-spacing:0.3em;margin-top:6px;}
  .brand-name .sub::before,.brand-name .sub::after{content:"";flex:1;height:2px;background:var(--brand);}

  .banner{position:absolute;left:0;top:250px;width:1120px;height:288px;}
  .status{
    position:absolute;left:58px;top:250px;height:288px;
    display:flex;align-items:center;
    font-family:"Anton",sans-serif;font-size:206px;line-height:1;color:#fff;letter-spacing:0.005em;
  }

  .contact{position:absolute;left:0;top:578px;width:100%;}
  .phone{position:absolute;left:124px;top:10px;display:flex;align-items:center;gap:40px;}
  .phone-icon{width:112px;height:112px;flex:none;}
  .phone-number{font-family:"Anton",sans-serif;font-size:118px;line-height:1;color:var(--ink);letter-spacing:0.01em;}
  .web{
    position:absolute;left:0;width:100%;top:132px;text-align:center;
    font-family:"Poppins",sans-serif;font-size:64px;line-height:1;color:var(--ink);
  }
</style>
</head>
<body>
<div class="sign">
  <div class="edge edge--top"></div>

  <div class="brand">
    <div class="brand-dot"></div>
    <div class="brand-name">
      <span class="main">MERIDIAN</span>
      <span class="sub">CREST REALTY</span>
    </div>
  </div>

  <svg class="banner" viewBox="0 0 1120 288" aria-hidden="true">
    <defs>
      <linearGradient id="bandShade" x1="0" y1="0" x2="0" y2="1">
        <stop offset="0" stop-color="#4b7371"/>
        <stop offset="0.47" stop-color="#4b7371"/>
        <stop offset="0.48" stop-color="#42625f"/>
        <stop offset="1" stop-color="#42625f"/>
      </linearGradient>
    </defs>
    <rect x="0" y="0" width="960" height="288" fill="url(#bandShade)"/>
    <circle cx="1040" cy="144" r="144" fill="#ffffff"/>
  </svg>
  <div class="status">FOR SALE</div>

  <div class="contact">
    <div class="phone">
      <svg class="phone-icon" viewBox="0 0 112 112" aria-hidden="true">
        <circle cx="56" cy="56" r="56" fill="var(--teal)"/>
        <path d="M40 30c3-2 6-1 7 2l5 10c1 3 0 5-2 6l-4 3c3 7 8 12 15 15l3-4c1-2 4-3 6-2l10 5c3 1 4 4 2 7l-4 6c-2 3-6 4-10 3-18-5-32-19-37-37-1-4 0-8 3-10z" fill="#fff"/>
        <path d="M62 34a18 18 0 0 1 16 16M64 24a28 28 0 0 1 24 24" stroke="#fff" stroke-width="4" fill="none" stroke-linecap="round"/>
      </svg>
      <span class="phone-number">555-214-7730</span>
    </div>
    <div class="web">meridiancrestrealty.com</div>
  </div>

  <div class="edge edge--bottom"></div>
</div>
</body>
</html>
```